Apparel store needs a cover for their seasonal catalogue

Every season the store creates a catalogue with a preview of the collection for the customers, the catalogue is printed and sent to 25 000 customers.We need a cover and back cover project for the upcoming winter season.Here is the current summer catalogue - https://www.la-botte.com/catalogue.shtmlFormat165mmx240mmAttached is some older issues, please note that the name LE SABOT MIRANVEL should be written on it as well as automne - hiver 2019 (fall-winter 19).

Target Market(s)

medium to high price consumers - male and female

Industry/Entity Type

Shoe Store

Colors

Designer to choose colors to be used in the design.

Requirements
Must have
• company name - LE SABOT MIRANVEL
• season - automne hiver 2019
• "Arty feel" to it
Nice to have
• Creative ideas - abstract themes
• As exemple I uploaded some older cover, but you do not have to follow the same patterns
Should not have
• product images

```html
<!DOCTYPE html>
<html lang="fr">
<head>
<meta charset="utf-8">
<title>Le Sabot Miranvel — Automne-Hiver 2019</title>
<link rel="stylesheet" href="https://fonts.googleapis.com/css2?family=Source+Serif+4:wght@400&display=swap">
<style>
  :root {
    --paper: #ffffff;
    --ink: #222222;
    --blush: #fdd6d8;
    --sky: #68cdf0;
    --aqua: #64d6e6;
    --mint: #7cf1cf;
  }
  html, body {
    margin: 0;
    padding: 0;
    width: 848px;
    height: 1200px;
    overflow: hidden;
    background: var(--paper);
  }
  .cover {
    position: relative;
    width: 848px;
    height: 1200px;
    background: var(--paper);
  }
  .cover-panel {
    position: absolute;
    left: 26px;
    top: 39px;
    width: 796px;
    height: 1120px;
    border-radius: 112px;
    background: linear-gradient(148deg,
      var(--blush) 0%,
      var(--blush) 18%,
      #bcd0e6 35%,
      var(--sky) 52%,
      var(--aqua) 66%,
      var(--mint) 90%,
      var(--mint) 100%);
  }
  .brand-name {
    position: absolute;
    left: 0;
    right: 0;
    top: 588px;
    margin: 0;
    text-align: center;
    font-family: "Source Serif 4", Georgia, serif;
    font-weight: 400;
    font-size: 52px;
    letter-spacing: 1px;
    color: var(--ink);
    white-space: nowrap;
  }
  .season {
    position: absolute;
    left: 0;
    right: 0;
    top: 1020px;
    margin: 0;
    text-align: center;
    font-family: "Source Serif 4", Georgia, serif;
    font-weight: 400;
    font-size: 23px;
    letter-spacing: 1px;
    color: var(--ink);
  }
</style>
</head>
<body>
  <main class="cover">
    <div class="cover-panel"></div>
    <h1 class="brand-name">LE SABOT MIRANVEL</h1>
    <p class="season">AUTOMNE - HIVER 2019</p>
  </main>
</body>
</html>
```